Business Cards for new orthopaedic surgery practice

My husband and I are starting our own orthopaedic surgery practice. We are looking for a business card that is uniform, but one will have my name/title and the other will have his. You can just create one design with my name on it for now. But when I choose your design as the winning design I will ask that you add another copy with his name/title.

We are looking for classy, simple, elite all in one. We like dark blues/a little gold/yellow. Something that goes with our logo. We want our logo incorporated. Here is all the info you need:
Business name: RV Bone & Vitality Center
Location: 38517 North Willowmere Ave
Maple Hollow, FL 33958
Phone: 954-218-4063
Fax: 954-582-7341
Email: info@myrvbonecare.example

Names: Lydia Vance, M.D.
Board Certified Hand and Upper Extremity Surgeon

Ebo Dansu, M.D.
Board Certified Hip & Knee Replacement/General Orthopaedic Surgeon

Can decide what you want to put on the back. Maybe a slogan:
Steady Hands. Strong Recovery

I am just going to upload our logo. The only thing is if we select you as the winning design, the location, and phone numbers may change. We will need your help to update that once fully solidified.

Industry/Entity Type

Medical

Contact Information for Business Card

Colors
0054AA
0677BA
7BADD7
CADEEF
E8F1F8
0094D4
00A9DD
6FCCEA
C7EBF8
E9F6FB

Requirements
Must have
• class, appeal,
Should not have
• We want to air on the side of masculine if we are looking at masculine vs. feminine feel. But we still want it classy, sophisticated, and something we will love

```html
<!DOCTYPE html>
<html lang="en">
<head>
<meta charset="utf-8">
<title>RV Bone &amp; Vitality Center – Business Cards</title>
<link href="https://fonts.googleapis.com/css2?family=Montserrat:wght@400;500;600;700&display=swap" rel="stylesheet">
<style>
  :root{
    --navy:#1b2a57;
    --gold:#c4a062;
    --mist:#cfd0db;
    --ink:#2a2d3a;
    --card:#ffffff;
    --stage:#3a3a3c;
  }
  *{box-sizing:border-box;margin:0;padding:0}
  html,body{width:1200px;height:875px;overflow:hidden}
  body{
    background:var(--stage);
    font-family:"Montserrat",Arial,sans-serif;
    display:flex;align-items:center;justify-content:center;gap:40px;
  }
  .card{
    position:relative;width:560px;height:320px;background:var(--card);
    border-radius:18px;overflow:hidden;
    box-shadow:0 14px 30px rgba(0,0,0,.35);
  }

  /* Appointment side */
  .appointment__title{
    position:absolute;top:34px;left:0;right:0;text-align:center;
    color:var(--navy);font-weight:700;font-size:19px;letter-spacing:.03em;
  }
  .field{position:absolute;display:flex;align-items:flex-end;gap:8px;
    font-size:12px;font-weight:500;color:var(--ink);letter-spacing:.04em}
  .field__line{flex:1;border-bottom:1.2px solid var(--navy);height:14px}
  .field--name{left:40px;right:40px;top:84px}
  .field--date{left:40px;width:260px;top:124px}
  .field--time{left:312px;right:40px;top:124px}
  .field--time .suffix{margin-left:4px}
  .week-label{position:absolute;left:40px;top:172px;font-size:14px;font-weight:600;
    color:var(--ink);letter-spacing:.03em}
  .days{position:absolute;left:40px;right:40px;top:204px;display:flex;justify-content:space-between}
  .day{display:flex;align-items:center;gap:6px;font-size:11px;color:var(--ink);letter-spacing:.04em}
  .box{width:14px;height:14px;border:1.5px solid var(--gold)}
  .slogan{position:absolute;left:0;right:0;bottom:42px;text-align:center;
    color:var(--gold);font-weight:600;font-size:16px}

  /* Contact side */
  .watermark{
    position:absolute;right:28px;top:24px;width:240px;
    font-weight:700;font-size:34px;line-height:1.05;color:var(--mist);opacity:.55;
    text-align:center;
  }
  .brand{position:absolute;left:34px;top:34px;display:flex;align-items:center;gap:10px}
  .brand__dot{width:18px;height:18px;border-radius:50%;background:var(--navy)}
  .brand__name{font-size:13px;font-weight:600;color:var(--navy);letter-spacing:.03em}
  .person{position:absolute;left:34px;top:128px}
  .person__name{font-size:24px;font-weight:700;color:var(--navy)}
  .person__name .credential{color:var(--gold)}
  .person__title{font-size:12px;color:var(--ink);line-height:1.35;margin-top:4px}
  .rule{position:absolute;left:34px;right:34px;top:208px;border-top:1px solid var(--navy)}
  .details{position:absolute;left:34px;top:222px;list-style:none;font-size:12px;color:var(--ink)}
  .details li{display:flex;align-items:center;gap:8px;line-height:21px}
  .details svg{width:11px;height:11px;fill:var(--gold)}
  .address{position:absolute;right:34px;top:222px;text-align:right;font-size:12px;color:var(--ink);line-height:21px;font-style:normal}
</style>
</head>
<body>

<section class="card appointment" aria-label="Appointment card">
  <h2 class="appointment__title">YOUR NEXT APPOINTMENT</h2>
  <div class="field field--name">NAME<span class="field__line"></span></div>
  <div class="field field--date">DATE<span class="field__line"></span></div>
  <div class="field field--time">TIME<span class="field__line"></span><span class="suffix">AM/PM</span></div>
  <div class="week-label">DAY OF THE WEEK</div>
  <div class="days">
    <span class="day"><span class="box"></span>MON</span>
    <span class="day"><span class="box"></span>TUE</span>
    <span class="day"><span class="box"></span>WED</span>
    <span class="day"><span class="box"></span>THU</span>
    <span class="day"><span class="box"></span>FRI</span>
    <span class="day"><span class="box"></span>SAT</span>
    <span class="day"><span class="box"></span>SUN</span>
  </div>
  <p class="slogan">Steady Hands. Strong Recovery</p>
</section>

<section class="card contact" aria-label="Business card">
  <div class="watermark" aria-hidden="true">RV Bone &amp;<br>Vitality<br>Center</div>
  <div class="brand">
    <span class="brand__dot"></span>
    <span class="brand__name">RV Bone &amp; Vitality Center</span>
  </div>
  <div class="person">
    <h1 class="person__name">Lydia Vance, <span class="credential">M.D.</span></h1>
    <p class="person__title">Board Certified Hand and<br>Upper Extremity Surgeon</p>
  </div>
  <div class="rule"></div>
  <ul class="details">
    <li><svg viewBox="0 0 24 24"><path d="M6.6 10.8a15 15 0 0 0 6.6 6.6l2.2-2.2a1 1 0 0 1 1-.25 11.4 11.4 0 0 0 3.6.57 1 1 0 0 1 1 1V20a1 1 0 0 1-1 1A17 17 0 0 1 3 4a1 1 0 0 1 1-1h3.5a1 1 0 0 1 1 1c0 1.25.2 2.45.57 3.57a1 1 0 0 1-.25 1z"/></svg>954-218-4063</li>
    <li><svg viewBox="0 0 24 24"><path d="M6 2h12v6H6zM3 9h18a1 1 0 0 1 1 1v8h-4v4H6v-4H2v-8a1 1 0 0 1 1-1zm5 8v3h8v-3z"/></svg>954-582-7341</li>
    <li><svg viewBox="0 0 24 24"><path d="M2 5h20v14H2zm2 2v.5l8 5 8-5V7l-8 5z"/></svg>info@myrvbonecare.example</li>
  </ul>
  <address class="address">38517 North Willowmere Ave<br>Maple Hollow, FL 33958</address>
</section>

</body>
</html>
```